Southern Plantskills Academy needs a modern website that oozes professionalism

Our current website is boring and looks like everyone elses. We need a modern website that says we are the best at plant operator training. We use Brontovex and Hiraketo equipment for our training. We train all over Australia in Civil Construction, Mining and Quarrying. We want to be the "Go to" website for all plant operator training in Australia.

Industry/Entity Type

Heavy Machinery Training

Colors
0054AA
0677BA
7BADD7
CADEEF
E8F1F8
FFF300
FFF600
FEFA6F
FFFEC7
FFFEE8

```html
<!DOCTYPE html>
<html lang="en">
<head>
<meta charset="utf-8">
<title>Southern Plantskills Academy — Plant Operator Training</title>
<link href="https://fonts.googleapis.com/css2?family=Open+Sans:wght@400;600;700&family=Work+Sans:wght@500;600;700&display=swap" rel="stylesheet">
<style>
:root{
  --navy:#1c3f77;
  --navy-deep:#13305f;
  --blue:#0054aa;
  --yellow:#f9c80e;
  --yellow-soft:#fde27a;
  --light:#eef2f7;
  --dark:#2b2e33;
  --ink:#2a2f38;
  --muted:#5f6670;
  --white:#ffffff;
}
*{box-sizing:border-box;margin:0;padding:0}
html,body{width:1200px;height:4377px;overflow:hidden}
body{position:relative;font-family:"Open Sans",sans-serif;color:var(--ink);background:var(--light)}
.abs{position:absolute}
.photo{position:absolute}
.eyebrow{position:absolute;left:0;width:100%;text-align:center;font-size:13px;color:var(--yellow);letter-spacing:.5px}
.eyebrow span{border-bottom:1px solid var(--yellow);padding-bottom:2px}
.section-title{position:absolute;left:0;width:100%;text-align:center;font-size:44px;font-weight:600;color:var(--navy)}
.btn-yellow{position:absolute;background:var(--yellow);color:var(--white);font-weight:600;display:flex;align-items:center;justify-content:center;gap:14px}

/* hero */
.hero{position:absolute;left:0;top:0;width:1200px;height:790px;overflow:hidden}
.hero-bg{left:0;top:0;width:1200px;height:790px;background:linear-gradient(180deg,#3b3d40 0%,#55524a 30%,#6d6655 55%,#4a4741 80%,#3a3936 100%)}
.hero-shade{position:absolute;inset:0;background:rgba(20,22,26,.35)}
.topbar{position:absolute;top:8px;left:0;width:1200px;height:18px;font-size:12px;color:var(--white)}
.topbar .item{position:absolute;display:flex;align-items:center;gap:5px}
.topbar .social{position:absolute;right:98px;display:flex;gap:11px}
.topbar .social i{display:block;width:13px;height:13px;background:var(--white);border-radius:2px}
.nav{position:absolute;left:87px;top:34px;width:1030px;height:86px;background:var(--white);border-radius:3px}
.brand{position:absolute;left:40px;top:28px;display:flex;align-items:center;gap:8px;font-weight:700;font-size:14px;color:var(--navy);letter-spacing:.4px}
.brand i{width:30px;height:30px;border-radius:50%;background:var(--navy);display:block}
.nav-links{position:absolute;top:35px;font-size:13px;font-weight:600;color:var(--ink)}
.hero-welcome{position:absolute;top:322px;left:0;width:1200px;text-align:center;color:var(--white);font-size:16px;font-weight:600}
.hero-title{position:absolute;top:360px;left:0;width:1200px;text-align:center;color:var(--white);font-size:64px;font-weight:600;line-height:88px}

/* services */
.card{position:absolute;top:1038px;width:325px;height:225px;background:var(--white);border-radius:4px;box-shadow:0 4px 14px rgba(0,0,0,.06)}
.card-img{position:absolute;top:1008px;width:290px;height:164px}
.card-icon{position:absolute;width:64px;height:64px;background:var(--navy);border-radius:32px 0 0 0;display:flex;align-items:center;justify-content:center}
.card-tag{position:absolute;top:1195px;width:325px;text-align:center;font-size:12px;color:var(--yellow)}
.card-name{position:absolute;top:1208px;width:325px;text-align:center;font-size:28px;font-weight:500;color:var(--navy)}
.experts{position:absolute;top:1318px;left:0;width:1200px;text-align:center;font-size:18px;color:var(--muted)}
.btn-white{position:absolute;left:490px;top:1365px;width:217px;height:63px;background:var(--white);color:var(--yellow);font-size:22px;font-weight:600;display:flex;align-items:center;justify-content:center;gap:20px;box-shadow:0 3px 12px rgba(0,0,0,.06)}

/* about */
.about{position:absolute;left:0;top:1475px;width:1200px;height:556px;background:linear-gradient(120deg,#2e2d2a,#4a4639 45%,#35342f)}
.about-shade{position:absolute;inset:0;background:rgba(25,25,28,.45)}
.about-frame{position:absolute;left:110px;top:75px;width:385px;height:385px;background:var(--navy-deep);border-radius:40px 6px 40px 6px}
.about-img{position:absolute;left:112px;top:88px;width:381px;height:370px;border-radius:30px 4px 30px 4px;background:linear-gradient(160deg,#b9c7d2,#e2d7c3 40%,#d97c33 65%,#3a5a98)}
.about-text{position:absolute;left:611px;width:520px;color:var(--white)}
.about-eyebrow{top:60px;font-size:13px;font-weight:600}
.about-eyebrow span{border-bottom:1px solid var(--white)}
.about-title{top:94px;font-size:42px;font-weight:700;line-height:52px}
.about-sub{top:224px;font-size:21px;font-weight:600}
.about-p{font-size:13px;line-height:21px;color:#e6e6e6}

/* projects */
.projects{position:absolute;left:130px;top:2229px;width:961px;height:376px}
.tile{position:absolute}
.tile-text{position:absolute;color:var(--white)}
.tile-text small{display:block;font-size:11px;font-weight:600;margin-bottom:6px}
.tile-text b{display:block;font-size:18px;font-weight:500;line-height:22px}
.tile-text .go{margin-top:12px;width:22px;height:22px;border:2px solid var(--white);border-radius:50%;display:flex;align-items:center;justify-content:center}
.see-more{position:absolute;left:508px;top:2653px;width:208px;height:48px;display:flex}
.see-more .lbl{width:160px;background:var(--yellow-soft);color:var(--white);font-size:12px;font-weight:600;display:flex;align-items:center;justify-content:center}
.see-more .arr{width:48px;background:var(--yellow);display:flex;align-items:center;justify-content:center}

/* testimonials */
.testi{position:absolute;left:0;top:2740px;width:1200px;height:558px;background:linear-gradient(110deg,#24272d,#3b3a34 50%,#2a2c31)}
.testi-shade{position:absolute;inset:0;background:rgba(25,27,32,.4)}
.t-eyebrow{position:absolute;left:90px;top:50px;font-size:13px;font-weight:600;color:var(--white)}
.t-eyebrow span{border-bottom:1px solid var(--white)}
.t-title{position:absolute;left:90px;top:84px;font-size:42px;font-weight:600;color:var(--white);font-family:"Work Sans",sans-serif}
.t-more{position:absolute;left:915px;top:90px;font-size:15px;font-weight:600;color:var(--white);display:flex;align-items:center;gap:10px}
.t-more i{width:38px;height:38px;background:var(--yellow);display:flex;align-items:center;justify-content:center}
.t-card{position:absolute;top:188px;width:490px;height:189px;background:rgba(120,124,130,.45);border-radius:3px;padding:34px 20px 0 20px;color:var(--white)}
.t-card h3{font-family:"Work Sans",sans-serif;font-size:27px;font-weight:600;margin-bottom:14px}
.t-card p{font-size:14px;line-height:24px}
.t-person{position:absolute;top:410px;display:flex;align-items:center;gap:20px;color:var(--white)}
.t-person .av{width:64px;height:64px;border-radius:50%;background:linear-gradient(135deg,#c9cfd6,#7b8794)}
.t-person b{display:block;font-family:"Work Sans",sans-serif;font-size:20px;font-weight:600}
.t-person small{font-size:14px}
.dots{position:absolute;top:518px;left:584px;display:flex;gap:12px}
.dots i{width:10px;height:10px;border-radius:50%;background:var(--white)}
.dots i.on{background:var(--yellow)}

/* contact */
.contact-card{position:absolute;left:138px;top:3522px;width:923px;height:455px;background:var(--white);border-radius:6px;overflow:hidden}
.contact-img{position:absolute;left:0;top:0;width:470px;height:455px;background:linear-gradient(150deg,#c7b79a,#9b8c73 35%,#2d4c87 70%,#1e3768)}
.form-brand{position:absolute;left:506px;top:50px;display:flex;align-items:center;gap:6px;font-size:10px;font-weight:700;color:var(--navy)}
.form-brand i{width:20px;height:20px;border-radius:50%;background:var(--navy)}
.form-title{position:absolute;left:512px;top:108px;font-size:29px;color:var(--navy)}
.field{position:absolute;border:1px solid #cfd3d8;border-radius:2px;font-size:12px;color:#6b7178;padding:10px 10px}
.send{position:absolute;left:512px;top:362px;width:360px;height:38px;background:var(--yellow);color:var(--white);font-size:12px;font-weight:600;display:flex;align-items:center;justify-content:center}

/* footer */
.footer-brand{position:absolute;top:4060px;left:0;width:1200px;display:flex;justify-content:center;align-items:center;gap:10px;font-size:19px;font-weight:700;color:var(--white);letter-spacing:.5px}
.footer-brand i{width:40px;height:40px;border-radius:50%;background:var(--white)}
.footer-links{position:absolute;top:4140px;font-size:14px;color:var(--white)}
.footer-rule{position:absolute;left:148px;top:4184px;width:910px;height:1px;background:rgba(255,255,255,.35)}
.f-item{position:absolute;top:4228px;display:flex;align-items:center;gap:14px;color:var(--white)}
.f-item .ic{width:54px;height:54px;border:1.5px solid var(--white);border-radius:50%;display:flex;align-items:center;justify-content:center}
.f-item small{font-size:11px;line-height:17px}
.f-item b{font-weight:400;font-size:13px;display:block}
.f-sep{position:absolute;top:4228px;width:1px;height:58px;background:rgba(255,255,255,.4)}
.bottom-bar{position:absolute;left:0;top:4322px;width:1200px;height:55px;background:var(--yellow)}
.bottom-bar .copy{position:absolute;left:147px;top:20px;font-size:12px;font-weight:600;color:var(--white)}
.bottom-bar .soc{position:absolute;right:140px;top:16px;display:flex;gap:8px}
.bottom-bar .soc i{width:24px;height:24px;border:1px solid var(--white);display:block}
</style>
</head>
<body>

<!-- HERO -->
<header class="hero">
  <div class="photo hero-bg" role="img" aria-label="Large yellow mining haul truck driving on a dusty quarry road"></div>
  <div class="hero-shade"></div>
  <div class="topbar">
    <div class="item" style="left:102px">
      <svg width="9" height="12" viewBox="0 0 9 12"><path d="M4.5 0C2 0 0 2 0 4.5 0 8 4.5 12 4.5 12S9 8 9 4.5C9 2 7 0 4.5 0zm0 6.3a1.8 1.8 0 110-3.6 1.8 1.8 0 010 3.6z" fill="#fff"/></svg>
      48 Quarry Road , Ballarat</div>
    <div class="item" style="left:363px">
      <svg width="12" height="9" viewBox="0 0 12 9"><rect width="12" height="9" fill="#fff"/><path d="M0 0l6 5 6-5" stroke="#555" fill="none"/></svg>
      hello@plantskills.example</div>
    <div class="item" style="left:578px">
      <svg width="10" height="10" viewBox="0 0 10 10"><path d="M2 0l2 2.5-1 1.5c.7 1.3 1.7 2.3 3 3l1.5-1L10 8l-1.5 2C4 9.5.5 6 0 1.5z" fill="#fff"/></svg>
      555 - 014 - 2288</div>
    <div class="social"><i></i><i></i><i></i><i></i></div>
  </div>
  <nav class="nav">
    <div class="brand"><i></i>Southern Plantskills Academy</div>
    <div class="nav-links" style="left:347px">HOME</div>
    <div class="nav-links" style="left:447px">ABOUT US</div>
    <div class="nav-links" style="left:584px">SERVICES</div>
    <div class="nav-links" style="left:710px">CONTACT US</div>
  </nav>
  <div class="hero-welcome">Welcome</div>
  <h1 class="hero-title">Empowering Operators,<br>Fueling Progress</h1>
  <div class="btn-yellow" style="left:524px;top:590px;width:156px;height:46px;font-size:15px">Contact us
    <svg width="18" height="12" viewBox="0 0 18 12"><path d="M0 6h16M11 1l5 5-5 5" stroke="#fff" stroke-width="1.6" fill="none"/></svg></div>
  <svg class="abs" style="left:0;top:640px" width="1200" height="150" viewBox="0 0 1200 150">
    <path d="M0 90 C150 40 400 40 640 70 C860 100 1050 110 1200 60 L1200 150 L0 150Z" fill="#eef2f7"/>
    <path d="M30 120 C200 60 420 40 640 70 C860 100 1040 110 1200 60 C1080 150 900 150 700 130 C500 110 300 140 30 120Z" fill="#f9c80e"/>
    <path d="M0 150 L0 118 C200 132 420 100 700 132 C900 150 1080 150 1200 70 L1200 150Z" fill="#eef2f7"/>
  </svg>
</header>

<!-- SERVICES -->
<section>
  <div class="eyebrow" style="top:856px"><span>WHAT WE DO</span></div>
  <h2 class="section-title" style="top:894px">Services We Offer</h2>

  <div class="card" style="left:85px"></div>
  <div class="card" style="left:436px"></div>
  <div class="card" style="left:786px"></div>

  <div class="photo card-img" style="left:103px;background:linear-gradient(135deg,#9cc3e6,#e6b62a 55%,#2b3345)" role="img" aria-label="Civil construction worker in hard hat beside an excavator"></div>
  <div class="photo card-img" style="left:454px;background:linear-gradient(135deg,#f2b35a,#f5e3c8 50%,#d9693a)" role="img" aria-label="Mining operator in orange hi-vis vest on a site"></div>
  <div class="photo card-img" style="left:804px;background:linear-gradient(135deg,#c88a4a,#e6b266 50%,#d49b3a)" role="img" aria-label="Yellow excavator loading a dump truck at a quarry"></div>

  <div class="card-icon" style="left:329px;top:1108px"><svg width="26" height="26" viewBox="0 0 26 26"><path d="M13 3l9 7-3 11H7L4 10z" stroke="#fff" stroke-width="1.6" fill="none"/></svg></div>
  <div class="card-icon" style="left:680px;top:1108px"><svg width="26" height="26" viewBox="0 0 26 26"><circle cx="13" cy="13" r="9" stroke="#fff" stroke-width="1.6" fill="none"/><path d="M9 13l3 3 5-6" stroke="#fff" stroke-width="1.6" fill="none"/></svg></div>
  <div class="card-icon" style="left:1030px;top:1108px"><svg width="26" height="26" viewBox="0 0 26 26"><path d="M5 21h16M8 21l6-10 4 4M14 11l3-5" stroke="#fff" stroke-width="1.6" fill="none"/></svg></div>

  <div class="card-tag" style="left:85px">OUR SERVICES</div>
  <div class="card-name" style="left:85px">Civil Construction</div>
  <div class="card-tag" style="left:436px">OUR SERVICES</div>
  <div class="card-name" style="left:436px">Mining</div>
  <div class="card-tag" style="left:786px">OUR SERVICES</div>
  <div class="card-name" style="left:786px">Quarrying</div>

  <p class="experts">The demanded experts in your area</p>
  <div class="btn-white">Contact us
    <svg width="26" height="18" viewBox="0 0 26 18"><path d="M0 9h24M16 1l8 8-8 8" stroke="#2f8fe0" stroke-width="2" fill="none"/></svg></div>
</section>

<!-- ABOUT -->
<section class="about">
  <div class="photo" style="inset:0;background:transparent" role="img" aria-label="Faded background of a yellow excavator at work"></div>
  <div class="about-shade"></div>
  <div class="about-frame"></div>
  <div class="photo about-img" role="img" aria-label="Operator in hard hat and orange vest gesturing beside a wheel loader"></div>
  <div class="about-text about-eyebrow"><span>WHO WE ARE</span></div>
  <h2 class="about-text about-title">Training Operators for<br>Industry Leaders</h2>
  <div class="about-text about-sub">Nurturing Operators, Cultivating Excellence</div>
  <p class="about-text about-p" style="top:268px">Lorem ipsum dolor sit amet, consectetur adipiscing elit, sed do eiusmod temp or incididunt ut labore et dolore magna aliqua. Ut enim ad minim veniam, quis laboris nisi ut aliquip ex ea commodo consequat.</p>
  <p class="about-text about-p" style="top:344px">Lorem ipsum dolor sit amet, consectetur adipiscing elit, sed do eiusmod temp or incididunt ut labore et dolore magna aliqua.</p>
  <div class="btn-yellow" style="left:609px;top:430px;width:154px;height:41px;font-size:15px;justify-content:flex-start;padding-left:16px">Contact us</div>
</section>

<!-- PROJECTS -->
<section>
  <div class="eyebrow" style="top:2096px"><span>GALLERY</span></div>
  <h2 class="section-title" style="top:2130px">Our Recent Projects</h2>
  <div class="projects">
    <div class="photo tile" style="left:0;top:0;width:493px;height:376px;background:linear-gradient(150deg,#9fb0c0,#6e7a6b 45%,#c9a53a 70%,#3e4c63)" role="img" aria-label="Smiling operator in yellow hard hat in front of a wheel loader"></div>
    <div class="tile" style="left:247px;top:188px;width:246px;height:188px;background:rgba(28,80,140,.92)"></div>
    <div class="tile-text" style="left:276px;top:214px"><small>PROJECT 1</small><b>OPERATOR TRAINING<br>IN THE SUBURBS OF<br>SYDNEY</b><div class="go"><svg width="8" height="10" viewBox="0 0 8 10"><path d="M2 1l4 4-4 4" stroke="#fff" stroke-width="1.6" fill="none"/></svg></div></div>

    <div class="tile" style="left:493px;top:0;width:231px;height:188px;background:var(--yellow)"></div>
    <div class="tile-text" style="left:513px;top:27px"><small>PROJECT 1</small><b>OPERATOR TRAINING<br>IN THE SUBURBS OF<br>SYDNEY</b><div class="go"><svg width="8" height="10" viewBox="0 0 8 10"><path d="M2 1l4 4-4 4" stroke="#fff" stroke-width="1.6" fill="none"/></svg></div></div>
    <div class="photo tile" style="left:493px;top:188px;width:231px;height:188px;background:linear-gradient(160deg,#b8c4cf,#5e6a75 45%,#d9b12c 75%,#4a4a45)" role="img" aria-label="Yellow mining machine working beside a quarry pool"></div>

    <div class="photo tile" style="left:724px;top:0;width:237px;height:188px;background:linear-gradient(170deg,#5a5c5e,#8a8a86 50%,#6f6e69)" role="img" aria-label="Muddy earthworks site with tyre tracks"></div>
    <div class="tile" style="left:724px;top:188px;width:237px;height:188px;background:var(--yellow)"></div>
    <div class="tile-text" style="left:749px;top:214px"><small>PROJECT 1</small><b>OPERATOR TRAINING<br>IN THE SUBURBS OF<br>SYDNEY</b><div class="go"><svg width="8" height="10" viewBox="0 0 8 10"><path d="M2 1l4 4-4 4" stroke="#fff" stroke-width="1.6" fill="none"/></svg></div></div>
  </div>
  <div class="see-more"><div class="lbl">SEE MORE</div><div class="arr"><svg width="18" height="12" viewBox="0 0 18 12"><path d="M0 6h16M11 1l5 5-5 5" stroke="#fff" stroke-width="1.8" fill="none"/></svg></div></div>
</section>

<!-- TESTIMONIALS -->
<section class="testi">
  <div class="photo" style="inset:0" role="img" aria-label="Dim background of an excavator on a construction site"></div>
  <div class="testi-shade"></div>
  <div class="t-eyebrow"><span>TESTIMONIALS</span></div>
  <h2 class="t-title">What our clients are saying</h2>
  <div class="t-more">More Testimonials <i><svg width="8" height="12" viewBox="0 0 8 12"><path d="M2 2l4 4-4 4" stroke="#fff" stroke-width="1.8" fill="none"/></svg></i></div>
  <div class="t-card" style="left:92px"><h3>Their service was excellent</h3><p>Lorem ipsum dolor sit amet, consectetur adipiscing elit, sed do eiusmod tempor incididunt ut labore et dolore magna aliqua. Ut enim ad minim</p></div>
  <div class="t-card" style="left:614px"><h3>Their service was excellent</h3><p>Lorem ipsum dolor sit amet, consectetur adipiscing elit, sed do eiusmod tempor incididunt ut labore et dolore magna aliqua. Ut enim ad minim</p></div>
  <div class="t-person" style="left:110px"><div class="av" role="img" aria-label="Client portrait"></div><div><b>Maren Holt</b><small>Client</small></div></div>
  <div class="t-person" style="left:631px"><div class="av" role="img" aria-label="Client portrait"></div><div><b>Declan Rourke</b><small>Client</small></div></div>
  <div class="dots"><i class="on"></i><i></i><i></i></div>
</section>

<!-- CONTACT + FOOTER -->
<section>
  <div class="eyebrow" style="top:3367px"><span>CONTACT US</span></div>
  <h2 class="section-title" style="top:3400px">Get in touch with us</h2>

  <svg class="abs" style="left:0;top:3780px" width="1200" height="545" viewBox="0 0 1200 545">
    <path d="M0 140 C150 30 300 10 420 20 L800 20 C950 10 1100 60 1200 150 L1200 545 L0 545Z" fill="#2a2c31"/>
    <path d="M1060 70 C1120 90 1170 120 1200 150 L1200 190 C1160 140 1110 110 1060 95Z" fill="#f9c80e"/>
  </svg>
  <div class="photo" style="left:0;top:3950px;width:1200px;height:372px;background:linear-gradient(110deg,rgba(60,58,52,.5),rgba(90,84,60,.35))" role="img" aria-label="Faded background of earthmoving machinery"></div>

  <div class="contact-card">
    <div class="photo contact-img" role="img" aria-label="Two operators in hard hats reviewing a tablet at a quarry with a wheel loader behind"></div>
    <div class="form-brand"><i></i>Southern Plantskills Academy</div>
    <div class="form-title">Please fill out the form</div>
    <div class="field" style="left:512px;top:172px;width:360px;height:36px">Name</div>
    <div class="field" style="left:512px;top:224px;width:173px;height:36px">Phone</div>
    <div class="field" style="left:699px;top:224px;width:173px;height:36px">Email</div>
    <div class="field" style="left:512px;top:278px;width:360px;height:70px">Message</div>
    <div class="send">Send</div>
  </div>

  <div class="footer-brand"><i></i>Southern Plantskills Academy</div>
  <div class="footer-links" style="left:352px">HOME</div>
  <div class="footer-links" style="left:446px">SERVICES</div>
  <div class="footer-links" style="left:552px">ABOUT US</div>
  <div class="footer-links" style="left:671px">TESTIMONIALS</div>
  <div class="footer-links" style="left:821px">BLOG</div>
  <div class="footer-rule"></div>

  <div class="f-item" style="left:173px"><div class="ic"><svg width="28" height="28" viewBox="0 0 28 28"><circle cx="14" cy="14" r="11" stroke="#fff" stroke-width="1.5" fill="none"/><path d="M3 14h22M14 3c-5 6-5 16 0 22M14 3c5 6 5 16 0 22" stroke="#fff" stroke-width="1.3" fill="none"/></svg></div><small>48 Quarry Road, Sebastopol<br>Ballarat, VIC 3350</small></div>
  <div class="f-sep" style="left:430px"></div>
  <div class="f-item" style="left:506px"><div class="ic"><svg width="20" height="28" viewBox="0 0 20 28"><rect x="3" y="2" width="14" height="24" rx="2" stroke="#fff" stroke-width="1.5" fill="none"/><path d="M8 22h4" stroke="#fff" stroke-width="1.5"/></svg></div><small><b>PHONE</b>(555) 014 2288</small></div>
  <div class="f-sep" style="left:749px"></div>
  <div class="f-item" style="left:826px"><div class="ic"><svg width="26" height="22" viewBox="0 0 26 22"><rect x="2" y="4" width="22" height="16" stroke="#fff" stroke-width="1.5" fill="none"/><path d="M2 4l11 9 11-9" stroke="#fff" stroke-width="1.5" fill="none"/></svg></div><small><b>EMAIL</b>info@plantskills.example</small></div>

  <div class="bottom-bar">
    <div class="copy">Southern Plantskills Academy</div>
    <div class="soc"><i></i><i></i><i></i><i></i></div>
  </div>
</section>

</body>
</html>
```